ReelBloom business card

We are a performing arts company providing training (to both kids and adults) as well as performers for events. We hope to bring joy and confidence on stage to the people we train, as well as joy to the audience when our artistes perform. Designs should convey the joy, confidence and vibrancy on stage. Design business card using the attached logo. Card to include name, mobile tel, email address, company address, and website. Double sided. To also include the following list of what the company does:
• Training & Enrichment
• Private & Corporate Entertainment
- Music composition & production

Industry/Entity Type

Training

Contact Information for Business Card

Card to include name, mobile tel, email address, company address, and website. Double sided. To also include the following list of what the company does:
• Training & Enrichment

Requirements
Nice to have
• Card need not be the traditional rectangular in shape but not too outrageous.

```html
<!DOCTYPE html>
<html lang="en">
<head>
<meta charset="utf-8">
<title>ReelBloom Business Card</title>
<link href="https://fonts.googleapis.com/css2?family=Arimo:wght@400;700&family=Playfair+Display:ital@1&display=swap" rel="stylesheet">
<style>
  :root {
    --backdrop: #e9e6e1;
    --card: #ffffff;
    --ink: #1e1e1e;
    --muted: #555555;
    --accent-orange: #f28a1e;
    --brand: #d81b72;
    --icon-bg: #1a1a1a;
    --icon-fg: #f5c400;
    --rule: #9a9a9a;
  }
  * { box-sizing: border-box; margin: 0; padding: 0; }
  html, body { width: 1200px; height: 886px; overflow: hidden; }
  body {
    background: var(--backdrop);
    font-family: "Arimo", Arial, sans-serif;
    color: var(--ink);
    position: relative;
  }
  .card {
    position: absolute;
    width: 540px;
    height: 310px;
    left: 330px;
    background: var(--card);
    border-radius: 22px;
    box-shadow: 0 6px 18px rgba(0,0,0,0.18);
    overflow: hidden;
  }
  .card--front { top: 110px; }
  .card--back { top: 466px; }

  .brand {
    display: flex;
    align-items: center;
    gap: 10px;
  }
  .brand__dot {
    width: 22px; height: 22px;
    border-radius: 50%;
    background: var(--brand);
  }
  .brand__name {
    font-family: "Arimo", Arial, sans-serif;
    font-weight: 700;
    color: var(--brand);
  }

  .front__left {
    position: absolute;
    left: 0; top: 0;
    width: 280px; height: 100%;
    display: flex;
    flex-direction: column;
    align-items: center;
    justify-content: center;
    gap: 34px;
  }
  .front__left .brand__name { font-size: 38px; }
  .services {
    list-style: none;
    text-align: center;
    font-size: 13px;
    line-height: 1.45;
    color: var(--ink);
  }
  .divider {
    position: absolute;
    left: 285px; top: 58px;
    width: 1px; height: 200px;
    background: linear-gradient(to bottom, transparent, var(--rule) 20%, var(--rule) 80%, transparent);
  }
  .front__right {
    position: absolute;
    left: 310px; top: 0;
    width: 220px; height: 100%;
    display: flex;
    flex-direction: column;
    justify-content: center;
    gap: 30px;
  }
  .person-name {
    font-family: "Playfair Display", Georgia, serif;
    font-style: italic;
    font-size: 28px;
    color: var(--accent-orange);
  }
  .contacts { list-style: none; display: flex; flex-direction: column; gap: 6px; }
  .contacts li {
    display: flex; align-items: center; gap: 8px;
    font-size: 13px; color: var(--ink);
    white-space: nowrap;
  }
  .contacts svg { flex: none; width: 16px; height: 16px; }

  .back__center {
    position: absolute; inset: 0;
    display: flex; align-items: center; justify-content: center;
  }
  .back__center .brand__name { font-size: 52px; }
  .back__center .brand__dot { width: 30px; height: 30px; }
</style>
</head>
<body>

<section class="card card--front" aria-label="Business card front">
  <div class="front__left">
    <div class="brand">
      <span class="brand__dot"></span>
      <span class="brand__name">ReelBloom</span>
    </div>
    <ul class="services">
      <li>Training &amp; Enrichment</li>
      <li>Private &amp; Corporate Entertainment</li>
      <li>Music composition &amp; production</li>
    </ul>
  </div>

  <div class="divider"></div>

  <div class="front__right">
    <p class="person-name">Your Name</p>
    <ul class="contacts">
      <li>
        <svg viewBox="0 0 16 16" aria-hidden="true"><rect width="16" height="16" rx="2" fill="var(--icon-bg)"/><rect x="5.5" y="3" width="5" height="10" rx="1" fill="none" stroke="var(--icon-fg)" stroke-width="1.3"/></svg>
        055-41260000
      </li>
      <li>
        <svg viewBox="0 0 16 16" aria-hidden="true"><rect width="16" height="16" rx="2" fill="var(--icon-bg)"/><path d="M4.5 4 L6.5 4 L7.2 6.2 L6 7.2 Q7 9.2 8.8 10 L9.8 8.8 L12 9.5 L12 11.5 Q7.5 12 4.5 7.5 Z" fill="var(--icon-fg)"/></svg>
        776-53817700
      </li>
      <li>
        <svg viewBox="0 0 16 16" aria-hidden="true"><rect width="16" height="16" rx="2" fill="var(--icon-bg)"/><rect x="3.5" y="5" width="9" height="6.5" fill="none" stroke="var(--icon-fg)" stroke-width="1.2"/><path d="M3.5 5 L8 8.6 L12.5 5" fill="none" stroke="var(--icon-fg)" stroke-width="1.2"/></svg>
        hello@reelbloom.com
      </li>
      <li>
        <svg viewBox="0 0 16 16" aria-hidden="true"><rect width="16" height="16" rx="2" fill="var(--icon-bg)"/><circle cx="8" cy="8" r="4.5" fill="none" stroke="var(--icon-fg)" stroke-width="1.2"/><path d="M3.5 8 H12.5 M8 3.5 Q5.5 8 8 12.5 M8 3.5 Q10.5 8 8 12.5" fill="none" stroke="var(--icon-fg)" stroke-width="1"/></svg>
        www.reelbloom.com
      </li>
      <li>
        <svg viewBox="0 0 16 16" aria-hidden="true"><rect width="16" height="16" rx="2" fill="var(--icon-bg)"/><path d="M8 13 Q4.5 9 4.5 6.8 A3.5 3.5 0 0 1 11.5 6.8 Q11.5 9 8 13 Z" fill="var(--icon-fg)"/><circle cx="8" cy="6.8" r="1.3" fill="var(--icon-bg)"/></svg>
        4521, elm grove street MI 3300 US
      </li>
    </ul>
  </div>
</section>

<section class="card card--back" aria-label="Business card back">
  <div class="back__center">
    <div class="brand">
      <span class="brand__dot"></span>
      <span class="brand__name">ReelBloom</span>
    </div>
  </div>
</section>

</body>
</html>
```